Heritage Hollow Business Cards

Require a business card design. <br/><br/>Needs to include logo (either round or long version) plus these details:<br/>Maya Torvell<br/>Heritage Hollow<br/>maya@kelvadtrading.com.au<br/>02 6481 7395<br/>PO Box Glenwarra NSW 2791<br/>www.heritagehollow.com.au<br/><br/>I need in an editable format so that I can create for multiple staff members. <br/><br/>

Target Market(s)

We are an online store selling renovation products to home owners are builders. Looking for a classic classy design.

Industry/Entity Type

Home And Garden

Contact Information for Business Card

Maya Torvell
Heritage Hollow
maya@kelvadtrading.com.au
02 6481 7395
PO Box Glenwarra NSW 2791
www.heritagehollow.com.au

Colors

Designer to choose colors to be used in the design.

Requirements
Must have
• Must include Logo.

```html
<!DOCTYPE html>
<html lang="en">
<head>
<meta charset="utf-8">
<title>Heritage Hollow Business Cards</title>
<link rel="stylesheet" href="https://fonts.googleapis.com/css2?family=Roboto:wght@400;700&display=swap">
<style>
  :root {
    --bg: #2e2e2e;
    --card: #1d1d1d;
    --silver: #d6d6d6;
    --silver-muted: #6a6a6a;
    --rule: #8a8a8a;
    --text: #e8e8e8;
  }
  * { margin: 0; padding: 0; box-sizing: border-box; }
  html, body { width: 1200px; height: 895px; overflow: hidden; }
  body {
    background: var(--bg);
    font-family: "Roboto", sans-serif;
    color: var(--text);
    display: flex;
    flex-direction: column;
    align-items: center;
    justify-content: center;
    gap: 40px;
  }
  .card {
    width: 620px;
    height: 354px;
    background: var(--card);
    border-radius: 4px;
    box-shadow: 0 10px 30px rgba(0,0,0,0.45);
    position: relative;
  }
  /* Front */
  .card--front { display: flex; align-items: center; justify-content: center; gap: 22px; }
  .front-mark {
    width: 110px; height: 110px;
    border: 2px solid var(--silver-muted);
    border-radius: 50%;
  }
  .front-name {
    font-size: 52px;
    font-weight: 400;
    color: var(--silver-muted);
    letter-spacing: 0.5px;
  }
  /* Back */
  .card--back { display: flex; align-items: center; padding: 0 40px 0 46px; }
  .brand {
    width: 210px;
    display: flex;
    align-items: center;
    gap: 14px;
  }
  .brand-mark {
    width: 64px; height: 64px; flex: none;
    border: 2px solid var(--silver);
    border-radius: 50%;
  }
  .brand-name {
    font-size: 22px;
    line-height: 1.15;
    font-weight: 400;
    color: var(--silver);
  }
  .divider {
    width: 1px; height: 190px;
    background: var(--rule);
    margin: 0 30px 0 14px;
  }
  .details { font-size: 14px; line-height: 1.35; }
  .person-name {
    font-size: 22px; font-weight: 700;
    letter-spacing: 1px; text-transform: uppercase;
  }
  .person-company { margin-bottom: 18px; }
  .address { margin-bottom: 18px; padding-left: 32px; }
  .contact-list { list-style: none; }
  .contact-list li { display: flex; align-items: center; gap: 10px; }
  .contact-list svg { width: 14px; height: 14px; flex: none; }
</style>
</head>
<body>
  <section class="card card--front" aria-label="Card front">
    <div class="front-mark"></div>
    <div class="front-name">Heritage Hollow</div>
  </section>

  <section class="card card--back" aria-label="Card back">
    <div class="brand">
      <div class="brand-mark"></div>
      <div class="brand-name">Heritage<br>Hollow</div>
    </div>
    <div class="divider"></div>
    <div class="details">
      <div class="person-name">Maya Torvell</div>
      <div class="person-company">Heritage Hollow</div>
      <div class="address">PO Box Glenwarra<br>NSW 2791</div>
      <ul class="contact-list">
        <li>
          <svg viewBox="0 0 16 16" aria-hidden="true"><path d="M4 1.5l2.2 3-1.4 1.6c.8 1.8 2.3 3.3 4.1 4.1l1.6-1.4 3 2.2-1.2 2.6C7.3 13.4 2.6 8.7 1.4 3.7z" fill="var(--text)"/></svg>
          <span>02 6481 7395</span>
        </li>
        <li>
          <svg viewBox="0 0 16 16" aria-hidden="true"><rect x="1.5" y="3.5" width="13" height="9" fill="none" stroke="var(--text)" stroke-width="1.4"/><path d="M1.5 3.5l6.5 5 6.5-5" fill="none" stroke="var(--text)" stroke-width="1.4"/></svg>
          <span>maya@kelvadtrading.com.au</span>
        </li>
        <li>
          <svg viewBox="0 0 16 16" aria-hidden="true"><circle cx="8" cy="8" r="6.3" fill="none" stroke="var(--text)" stroke-width="1.3"/><ellipse cx="8" cy="8" rx="2.6" ry="6.3" fill="none" stroke="var(--text)" stroke-width="1.1"/><path d="M1.7 8h12.6" stroke="var(--text)" stroke-width="1.1"/></svg>
          <span>www.heritagehollow.com.au</span>
        </li>
      </ul>
    </div>
  </section>
</body>
</html>
```